Orthodox Christian Youth Conference Flyer/Agenda

We are seeking a designer to help us take our award winning conference to the next level with a pamphlet that will outline the agenda of the 3 day conference but will also include pictures, illustrations, and visuals so that we build some excitement and interest. We also need to be able to make adjustments and corrections to the pamphlet's text, leading up to the conference and would like it in a file that could permit us to edit it without having to bother you!

Target Market(s)

To be used to promote conference and agenda

Industry/Entity Type

Christian

Font styles to use
Serif
Sans Serif

Requirements
Must have
• include logo, photos and visuals

```html
<!DOCTYPE html>
<html lang="en">
<head>
<meta charset="utf-8">
<title>Youth and Family Conference Pamphlet</title>
<link href="https://fonts.googleapis.com/css2?family=Oswald:wght@500;700&family=Open+Sans:wght@400;600;700&display=swap" rel="stylesheet">
<style>
:root{
  --green-dark:#3f5a1d;
  --green:#7d9a2a;
  --lime:#a9bd38;
  --pale:#eef2dc;
  --ink:#333;
  --grey:#8a8a8a;
  --photo-warm:#8c7a62;
  --photo-dark:#4e4a44;
  --bg:#ffffff;
}
*{box-sizing:border-box;margin:0;padding:0}
html,body{width:889px;height:1200px;overflow:hidden;background:var(--bg);font-family:"Open Sans",Arial,sans-serif;color:var(--ink)}
.canvas{position:relative;width:889px;height:1200px}
.page{position:absolute;background:#fff;box-shadow:0 1px 5px rgba(0,0,0,.35);overflow:hidden}
.page-label{position:absolute;font:700 13px "Open Sans",Arial,sans-serif;letter-spacing:1px;color:#222;text-align:center}
.photo{position:absolute}
.tiny{font-size:5.2px;line-height:7px;color:var(--ink)}
.h-band{font-family:"Oswald",Arial,sans-serif;text-transform:uppercase;font-weight:700}
/* page 1 */
.p1{left:44px;top:6px;width:390px;height:497px}
.p1 .parish{position:absolute;left:14px;top:12px;width:160px;font:600 7px "Open Sans",sans-serif;color:var(--green)}
.p1 .title{position:absolute;left:14px;top:30px;width:175px;font:700 13px/15px "Oswald",sans-serif;color:var(--green-dark);text-transform:uppercase}
.p1 .subtitle{position:absolute;left:14px;top:100px;width:170px;font:600 6px/8px "Open Sans",sans-serif;color:var(--green)}
.p1 .green-band{position:absolute;left:0;top:130px;width:390px;height:24px;background:var(--green)}
.p1 .diag{position:absolute;right:-40px;top:150px;width:200px;height:330px;background:linear-gradient(160deg,var(--lime),var(--green));transform:skewX(-8deg)}
.p1 .badge{position:absolute;left:58px;top:142px;width:140px;height:58px;border-radius:30px;background:#fff;border:3px solid var(--lime);text-align:center;padding-top:10px;font:700 14px/17px "Oswald",sans-serif;color:var(--green-dark)}
.p1 .agenda{position:absolute;left:12px;top:210px;width:225px;height:250px;background:#fff;padding:6px}
.agenda h4{font:700 6.5px "Open Sans",sans-serif;color:var(--green-dark);margin:4px 0 2px}
.p1 .footer{position:absolute;left:0;bottom:0;width:390px;height:22px;background:var(--green-dark);color:#fff;font:600 6px/22px "Open Sans",sans-serif;padding-left:10px}
/* page 2 */
.p2{left:450px;top:6px;width:408px;height:497px}
.p2 .donate{position:absolute;left:92px;top:30px;width:110px;height:110px;background:var(--pale);border:2px solid var(--lime);text-align:center;padding:8px 6px}
.p2 .donate b{display:block;font:700 15px "Oswald",sans-serif;color:var(--green-dark);margin-bottom:6px}
.p2 .intro{position:absolute;left:210px;top:120px;width:188px}
.p2 .hotel{position:absolute;left:210px;top:185px;width:188px;height:60px;background:var(--pale);padding:4px}
.p2 .other{position:absolute;left:0;top:262px;width:408px;height:26px;background:linear-gradient(90deg,var(--lime),var(--green))}
.p2 .other-badge{position:absolute;left:150px;top:250px;width:110px;height:48px;background:#fff;border:3px solid var(--green);border-radius:24px;text-align:center;padding-top:6px;font:700 12px/14px "Oswald",sans-serif;color:var(--green-dark)}
.p2 .info{position:absolute;top:310px;width:185px;height:170px;background:var(--pale);padding:6px}
.info h4{font:700 6.5px "Open Sans",sans-serif;color:var(--green-dark);margin:3px 0 2px}
/* page 3 */
.p3{left:222px;top:563px;width:435px;height:607px}
.p3 .desc{position:absolute;left:18px;top:14px;width:150px;height:60px;background:var(--green-dark);color:#fff;font:700 17px/21px "Oswald",sans-serif;padding:9px 10px;text-transform:uppercase}
.p3 .lead{position:absolute;left:14px;top:112px;width:405px;height:20px;background:var(--green);color:#fff;padding:3px 6px}
.p3 .lead .tiny{color:#fff}
.p3 .faq{position:absolute;left:14px;top:140px;width:405px}
.p3 .faq h4{font:700 8px "Oswald",sans-serif;color:var(--green-dark);margin-bottom:3px}
.p3 .faq p{margin-bottom:4px}
.p3 .lower{position:absolute;left:14px;top:378px;width:200px}
</style>
</head>
<body>
<div class="canvas">

  <!-- PAGE 1 -->
  <section class="page p1">
    <p class="parish">Holy Trinity Orthodox Parish</p>
    <h1 class="title">The 2015 Orthodox Christian Youth and Family Conference in Cedar Hill, Pennsylvania</h1>
    <p class="subtitle">Conference Theme: "Be Transformed" &middot; October 16–18, 2015 &middot; Hosted at the parish hall and grounds</p>
    <div class="photo" role="img" aria-label="Photo of clergy and faithful in procession" style="left:195px;top:0;width:195px;height:130px;background:linear-gradient(135deg,var(--photo-warm),var(--photo-dark))"></div>
    <div class="green-band"></div>
    <div class="diag"></div>
    <div class="photo" role="img" aria-label="Photo of young people at the conference" style="left:255px;top:220px;width:120px;height:90px;background:linear-gradient(135deg,#b7a58a,#6e6252);border:2px solid #fff"></div>
    <div class="photo" role="img" aria-label="Photo of a church service" style="left:255px;top:325px;width:120px;height:90px;background:linear-gradient(135deg,#c9b48a,#5d5140);border:2px solid #fff"></div>
    <div class="badge">PRELIMINARY<br>PROGRAM AGENDA</div>
    <div class="agenda">
      <h4>Thursday October 15th, 2015 "Arrival and Opening Night"</h4>
      <p class="tiny">4:00 pm – Arrival and registration at the parish hall<br>6:00 pm – Welcome dinner with families and clergy<br>7:30 pm – Vespers and opening remarks<br>8:30 pm – Icebreaker games for youth groups</p>
      <h4>Friday October 16th, 2015 "Teachings, Faith and Fellowship"</h4>
      <p class="tiny">8:00 am – Morning prayers and breakfast<br>9:30 am – Keynote talk on living the faith today<br>11:00 am – Small group discussions by age<br>12:30 pm – Lunch on the grounds<br>2:00 pm – Workshops: music, service and prayer<br>5:00 pm – Free time and sports<br>7:00 pm – Evening dinner and talent show</p>
      <h4>Saturday October 17th, 2015 "Tours and Lake Visit"</h4>
      <p class="tiny">8:00 am – Morning prayers and breakfast<br>10:00 am – Guided tour of the historic church<br>1:00 pm – Lake picnic and outdoor games<br>6:00 pm – Great Vespers and confession<br>8:00 pm – Youth bonfire and singing</p>
      <h4>Sunday October 18th, 2015 "Divine Liturgy, Brunch and Farewell"</h4>
      <p class="tiny">9:00 am – Divine Liturgy<br>11:30 am – Farewell brunch and closing words</p>
    </div>
    <div class="footer">Optional Activity: Sunday afternoon hike at the state park and scenic river walk</div>
  </section>
  <div class="page-label" style="left:44px;top:518px;width:390px">PAGE 1</div>

  <!-- PAGE 2 -->
  <section class="page p2">
    <div class="photo" role="img" aria-label="Photo of a priest blessing the faithful" style="left:8px;top:8px;width:78px;height:130px;background:linear-gradient(160deg,#d3c3a0,#7a6a52)"></div>
    <div class="donate">
      <b>DONATE</b>
      <p class="tiny">Support our youth by helping cover meals, lodging and travel for families in need. Every gift helps.</p>
    </div>
    <div class="photo" role="img" aria-label="Icon of a saint" style="left:210px;top:8px;width:58px;height:80px;background:linear-gradient(160deg,#c89a4a,#6b4a22)"></div>
    <div class="photo" role="img" aria-label="Photo of a church interior" style="left:272px;top:8px;width:58px;height:80px;background:linear-gradient(160deg,#b99a6a,#5a4630)"></div>
    <div class="photo" role="img" aria-label="Photo of a historic theatre hall" style="left:334px;top:8px;width:66px;height:80px;background:linear-gradient(160deg,#a84a3a,#4a2a22)"></div>
    <div class="intro">
      <p class="tiny" style="color:var(--green-dark);font-weight:700">Our parish welcomes families from every diocese for three days of prayer, learning and friendship.</p>
      <p class="tiny">Meals are served in the parish hall. Bring comfortable shoes, a jacket for the lake and your prayer book.</p>
    </div>
    <div class="hotel">
      <h4 style="font:700 6.5px 'Open Sans',sans-serif;color:var(--green-dark)">Lodging</h4>
      <p class="tiny">Rooms are reserved at nearby inns under the conference block. Ask for the youth rate when booking before October 1st.</p>
    </div>
    <div class="photo" role="img" aria-label="Photo of conference guests" style="left:8px;top:150px;width:194px;height:100px;background:linear-gradient(135deg,#9a8d78,#514a40)"></div>
    <div class="other"></div>
    <div class="other-badge">OTHER<br>INFORMATION</div>
    <div class="info" style="left:10px">
      <h4>Registration</h4>
      <p class="tiny">Register online or at the parish office. Youth $45, adults $60, families $150. Fee covers meals and materials.</p>
      <h4>Contact</h4>
      <p class="tiny">Conference office: (555) 014-2290<br>youth@holytrinityparish.org<br>120 Chapel Road, Cedar Hill, PA</p>
      <h4>Transportation and Parking</h4>
      <p class="tiny">Free parking behind the parish hall. Shuttles run to the lake and tour sites each day.</p>
    </div>
    <div class="info" style="left:213px">
      <h4>What to Bring</h4>
      <p class="tiny">Bible, prayer book, water bottle, sun hat, warm layers and an open heart.</p>
      <h4>Volunteers</h4>
      <p class="tiny">We need helpers for meals, setup and child care. Sign up at the welcome table.</p>
      <h4>Special Thanks</h4>
      <p class="tiny">Our clergy, parish council, sisterhood and every family who makes this gathering possible.</p>
    </div>
  </section>
  <div class="page-label" style="left:450px;top:518px;width:408px">PAGE 2</div>

  <!-- PAGE 3 -->
  <section class="page p3">
    <div class="photo" role="img" aria-label="Photo of a lake landscape with trees" style="left:0;top:0;width:435px;height:105px;background:linear-gradient(180deg,#9fb36a,#5e7233)"></div>
    <div class="desc">Description<br>of Event</div>
    <div class="lead"><p class="tiny">Three days of worship, workshops and fellowship for youth, parents and clergy in the heart of the hills.</p></div>
    <div class="faq">
      <h4>FAQS</h4>
      <p class="tiny"><b>Who may attend?</b> All Orthodox youth from middle school through college, together with parents, godparents and clergy, are warmly welcome. Guests exploring the faith may join as well.</p>
      <p class="tiny"><b>What happens each day?</b> Days open with prayer, continue with talks and workshops, and close with services and evening fellowship. Free time allows for sports, crafts and quiet reflection.</p>
      <p class="tiny"><b>Is child care offered?</b> Yes. Trained volunteers lead a program for younger children during talks so that parents may take part fully.</p>
      <p class="tiny"><b>Where do we sleep?</b> Families stay at partner inns nearby. A limited number of host homes are open for college students on request.</p>
      <p class="tiny"><b>What should we wear?</b> Modest, comfortable clothing for the day and church attire for services. Evenings by the lake can be cool.</p>
      <p class="tiny"><b>Can we help?</b> Volunteers, donors and cooks are always needed. Speak with the office to learn how you can serve.</p>
    </div>
    <div class="lower">
      <p class="tiny">Past conferences gathered over two hundred guests. This year we add a music track, a service project in town and a family night of stories from parish elders.</p>
      <p class="tiny">Come and see how faith grows when we gather together.</p>
    </div>
    <div class="photo" role="img" aria-label="Photo of youth in a discussion group" style="left:14px;top:440px;width:190px;height:150px;background:linear-gradient(135deg,#b9a685,#5f5342)"></div>
    <div class="photo" role="img" aria-label="Photo of a priest speaking at a lectern" style="left:222px;top:378px;width:200px;height:212px;background:linear-gradient(135deg,#c2b08e,#4f4536)"></div>
  </section>
  <div class="page-label" style="left:222px;top:1178px;width:435px">PAGE 3</div>

</div>
</body>
</html>
```